Website for legal expungement services with button to qualify/disqualify potential clients

Brightpath Record Renewal, LLC is a law firm focusing in legal expungement servcies (allowing people to erase criminal court records, police records, proseution files, etc). I want a more modern look which exudes confidence in the services. I am looking for a clean website that looks very polished. I want to keep the pages to a minimum, as I want the page not so much to answer questions, but to direct traffic to contact the law office. I would like the main focus point to be an button which would take a client through a series of questions to see if they would qualify for the services; this serves two purposes 1) to collect contact info for future marketing via email and 2) eliminate individuals who we are currently unable to help. A current theme that I have played around with are "Change so much, you'll need to reintroduce yourself" alongside a picture of a guys hand outstretched.
On the landing page, I would like a very brief and to the point explanation of what the service would be (i.e. "Leave your past in the past; expunge all your criminal records" ), followed by a list of benefits that it provides. (NB: included is a file "law post card-02" that includes the main benefits to expungement). Also included are two logo files for a more updated logo I currently use ("BRR Logo" and BRR Logo2") (NB: I'm open to revisions on this as well). Lastly, I've had two very minor 'ads' that I did ("postcard back" and "KVT Ad") that I like the idea of.

Target Market(s)

Middle/upper-middle class, mostly male, people with a criminal record or criminal accusation

Industry/Entity Type

Legal Services

Coding

Coded - Design and coding required

Requirements
Must have
• Button that attracts attention up front (possibly stand out coloring) to click to open up a series of questions to qualify/eliminate prospects, and simultaneously gather their info. Also, must be mobile friendly.

```html
<!DOCTYPE html>
<html lang="en">
<head>
<meta charset="utf-8">
<title>Brightpath Record Renewal</title>
<link rel="stylesheet" href="https://fonts.googleapis.com/css2?family=Old+Standard+TT:wght@400&family=Poppins:wght@400;500&display=swap">
<style>
:root{
  --blue:#5079a5;
  --navy:#35577c;
  --ink:#243b58;
  --gold:#d4a52a;
  --text:#3d3d3d;
  --line:#7f96b2;
  --dark:#262626;
  --darker:#1c1c1c;
  --white:#ffffff;
}
*{margin:0;padding:0;box-sizing:border-box}
html,body{width:1200px;height:4264px;overflow:hidden}
body{position:relative;background:var(--white);font-family:"Poppins",sans-serif;color:var(--text)}
.abs{position:absolute}
.serif{font-family:"Old Standard TT",serif}
.btn{position:absolute;display:flex;align-items:center;justify-content:center;background:var(--blue);color:var(--white);font-family:"Old Standard TT",serif;font-size:20px;letter-spacing:.5px}
.social{display:flex;gap:18px}
.social span{width:20px;height:20px;background:currentColor;border-radius:3px}

.topbar{left:0;top:0;width:1200px;height:50px;background:var(--blue);color:var(--white)}
.topbar .social{position:absolute;left:74px;top:16px}
.topbar .phone{position:absolute;right:73px;top:9px;font-size:25px;display:flex;align-items:center;gap:10px}

.header{left:0;top:50px;width:1200px;height:107px}
.brand{position:absolute;display:flex;align-items:center;gap:16px}
.brand-square{width:22px;height:22px;background:var(--blue);flex:0 0 22px}
.brand-name{font-family:"Old Standard TT",serif;font-size:19px;line-height:1.15;color:var(--ink)}
.nav{position:absolute;top:48px;font-size:13px;color:#222}
.nav.active{color:var(--blue);font-weight:500}

.hero{left:0;top:157px;width:1200px;height:580px;background:linear-gradient(180deg,#9fb3c6 0%,#bccad6 40%,#8ea5bb 100%)}
.hero h1{position:absolute;left:0;top:172px;width:1200px;text-align:center;font-family:"Old Standard TT",serif;font-weight:400;font-size:52px;line-height:60px;color:var(--white)}
.hero .book{left:445px;top:340px;width:310px;height:58px;background:var(--gold);font-size:21px}

.welcome-frame{left:74px;top:861px;width:1052px;height:429px;border:1.5px solid var(--line)}
.welcome-title{left:254px;top:806px;width:692px;background:var(--white);text-align:center;font-size:47px;line-height:52px;color:var(--ink)}
.welcome-text{left:130px;top:931px;width:940px;text-align:center;font-size:17px;line-height:32.5px}
.welcome-text p+p{margin-top:16px}

.section-title{left:0;width:1200px;text-align:center;font-size:47px;color:var(--ink)}

.photo{position:absolute}
.service-head{font-size:48px;line-height:52px;color:var(--ink)}
.service-text{font-size:17px;line-height:32.5px}

.benefits{left:0;top:2444px;width:1200px;height:568px;background:var(--navy)}
.benefit{position:absolute;width:328px;height:90px;border:1px solid #6a86a7;display:flex;align-items:center;gap:20px;padding-left:20px;color:var(--white);font-size:15.5px;line-height:23px}
.benefit .icon{flex:0 0 66px;width:66px;height:66px;border-radius:50%;background:var(--white);display:flex;align-items:center;justify-content:center}

.cases-frame{left:526px;top:3085px;width:600px;height:503px;border:1.5px solid var(--line)}
.cases-list{list-style:none;font-size:17px;line-height:26px}
.cases-list li{position:absolute;display:flex;gap:14px}

.cta{left:0;top:3666px;width:1200px;height:227px;background:var(--gold);color:var(--white)}
.cta p{position:absolute;left:74px;top:52px;font-family:"Old Standard TT",serif;font-size:33px;line-height:40px}
.cta .phone{position:absolute;left:784px;top:80px;font-family:"Old Standard TT",serif;font-size:46px;display:flex;align-items:center;gap:24px}

.footer{left:0;top:3893px;width:1200px;height:311px;background:var(--dark);color:var(--white)}
.footer .brand-square{background:var(--white)}
.footer .brand-name{color:var(--white)}
.footer h4{position:absolute;font-family:"Old Standard TT",serif;font-weight:400;font-size:20px}
.footer .link{position:absolute;font-size:15px}
.footer .contact{position:absolute;left:794px;display:flex;gap:16px;font-size:15px;line-height:22px}
.copyright{left:0;top:4204px;width:1200px;height:60px;background:var(--darker);color:#bbb;font-size:13px;text-align:center;line-height:60px}
</style>
</head>
<body>

<div class="abs topbar">
  <div class="social" aria-label="Social links"><span></span><span></span><span></span><span></span><span></span></div>
  <div class="phone serif">
    <svg width="22" height="24" viewBox="0 0 22 24" fill="none" stroke="#fff" stroke-width="2"><path d="M5 3l4 1 1 5-3 2c1 3 3 5 6 6l2-3 5 1 1 4c-1 2-3 3-5 3C8 21 2 14 2 7c0-2 1-3 3-4z" fill="#fff"/><path d="M15 3c2 1 3 2 4 4M14 7c1 0 2 1 2 2"/></svg>
    505-555-0142
  </div>
</div>

<header class="abs header">
  <div class="brand" style="left:74px;top:30px">
    <span class="brand-square"></span>
    <span class="brand-name">BRIGHTPATH RECORD<br>RENEWAL</span>
  </div>
  <a class="nav active" style="left:473px">HOME</a>
  <a class="nav" style="left:556px">ABOUT US</a>
  <a class="nav" style="left:665px">SERVICES</a>
  <a class="nav" style="left:771px">BENEFITS</a>
  <a class="nav" style="left:872px">CASES</a>
  <a class="nav" style="left:958px">BLOG</a>
  <a class="nav" style="left:1036px">CONTACT US</a>
</header>

<section class="abs hero" role="img" aria-label="Man seen from behind raising both arms toward a cloudy sky">
  <h1>CHANGE SO MUCH, YOU'LL NEED TO<br>REINTRODUCE YOURSELF</h1>
  <a class="btn book">BOOK AN APPOINTMENT</a>
</section>

<div class="abs welcome-frame"></div>
<h2 class="abs welcome-title serif" style="font-weight:400">WELCOME TO BRIGHTPATH<br>RECORD RENEWAL</h2>
<div class="abs welcome-text">
  <p>ed ut perspiciatis unde omnis iste natus error sit voluptatem accusantium doloremque laudantium, totam rem aperiam, eaque ipsa quae ab illo inventore veritatis et quasi architecto beatae vitae dicta sunt explicabo. Nemo enim ipsam voluptatem quia voluptas sit aspernatur aut odit aut fugit, sed quia consequuntur magni dolores eos qui ratione voluptatem sequi nesciunt.</p>
  <p>Eerspiciatis unde omnis iste natus error sit voluptatem accusantium doloremque laudantium, totam rem aperiam, eaque ipsa quae ab illo inventore veritatis et quasi architecto beatae vitae dicta sunt explicabo. Nemo enim ipsam voluptatem quia voluptas sit aspernatur aut odit aut fugit.</p>
</div>
<a class="btn" style="left:511px;top:1198px;width:178px;height:58px">READ MORE</a>

<h2 class="abs section-title serif" style="top:1350px;font-weight:400">OUR SERVICES</h2>

<div class="photo" style="left:0;top:1448px;width:600px;height:459px;background:linear-gradient(135deg,#3a3632 0%,#6a625a 45%,#e6e4e0 60%,#f2efec 100%)" role="img" aria-label="Criminal record document stamped for expungement beside a gavel and glasses"></div>
<div class="abs" style="left:642px;top:1503px;width:500px">
  <h3 class="service-head serif" style="font-weight:400">Leave your past in<br>the past</h3>
  <p class="service-text" style="margin-top:26px">Eerspiciatis unde omnis iste natus error sit voluptatem accusantium doloremque laudantium, &nbsp;totam rem aperiam, eaque ipsa quae ab illo inventore veritatis et quasi architecto beatae vitae dicta sunt.</p>
</div>
<a class="btn" style="left:642px;top:1787px;width:177px;height:57px">READ MORE</a>

<div class="abs" style="left:74px;top:1961px;width:500px">
  <h3 class="service-head serif" style="font-weight:400">Expunge all your<br>criminal records</h3>
  <p class="service-text" style="margin-top:26px">Eerspiciatis unde omnis iste natus error sit voluptatem accusantium doloremque laudantium, &nbsp;totam rem aperiam, eaque ipsa quae ab illo inventore veritatis et quasi architecto beatae vitae dicta sunt.</p>
</div>
<a class="btn" style="left:74px;top:2246px;width:178px;height:57px">READ MORE</a>
<div class="photo" style="left:600px;top:1907px;width:600px;height:458px;background:linear-gradient(120deg,#4a2e1e 0%,#7a5036 35%,#e8e4df 55%,#8a5a3c 100%)" role="img" aria-label="Hands tearing a paper note reading criminal record"></div>

<section class="abs benefits">
  <h2 class="abs section-title serif" style="top:64px;color:var(--white);font-weight:400">BENEFITS OF EXPUNGEMENT</h2>
  <div class="benefit" style="left:74px;top:149px"><span class="icon"><svg width="34" height="34" viewBox="0 0 34 34" fill="none" stroke="#35577c" stroke-width="1.6"><rect x="8" y="5" width="20" height="13"/><circle cx="18" cy="11.5" r="3"/><path d="M3 22c4-2 8-1 11 1h8c2 0 2 3 0 3h-7M3 29l10-1 16-7"/></svg></span>More and better job opportunities leading to higher income</div>
  <div class="benefit" style="left:434px;top:149px"><span class="icon"><svg width="34" height="34" viewBox="0 0 34 34" fill="none" stroke="#35577c" stroke-width="1.6"><rect x="6" y="4" width="18" height="25"/><path d="M10 10h10M10 15h10M10 20h6M28 8L17 27l-2 3 1-4L27 7z"/></svg></span>Better education opportunities</div>
  <div class="benefit" style="left:798px;top:149px"><span class="icon"><svg width="34" height="34" viewBox="0 0 34 34" fill="none" stroke="#35577c" stroke-width="1.6"><path d="M10 5h14v8a7 7 0 01-14 0zM10 8H5c0 5 3 7 5 7M24 8h5c0 5-3 7-5 7M17 20v5M11 29h12v-4H11z"/></svg></span>Qualifying for government assistance programs</div>
  <div class="benefit" style="left:74px;top:273px"><span class="icon"><svg width="34" height="34" viewBox="0 0 34 34" fill="none" stroke="#35577c" stroke-width="1.6"><path d="M5 30h24M8 30V14h6v16M20 30V8h6v22M17 4l-3 4h6z"/></svg></span>Loan qualification and better &nbsp;loan rates</div>
  <div class="benefit" style="left:434px;top:273px"><span class="icon"><svg width="34" height="34" viewBox="0 0 34 34" fill="none" stroke="#35577c" stroke-width="1.6"><path d="M9 7l8 8-4 4-8-8zM15 13l12 12-2 2-12-12M5 30h14"/></svg></span>Removing the stigma of having a criminal record</div>
  <div class="benefit" style="left:798px;top:273px"><span class="icon"><svg width="34" height="34" viewBox="0 0 34 34" fill="none" stroke="#35577c" stroke-width="1.6"><path d="M7 4h16v24H7zM11 10h8M11 15h8M11 20h4"/><circle cx="24" cy="24" r="5"/></svg></span>Lower insurance premiums</div>
  <div class="benefit" style="left:255px;top:399px"><span class="icon"><svg width="34" height="34" viewBox="0 0 34 34" fill="none" stroke="#35577c" stroke-width="1.6"><path d="M17 3l11 4v9c0 7-5 12-11 15C11 28 6 23 6 16V7z"/><rect x="13" y="15" width="8" height="7"/><path d="M14 15v-2a3 3 0 016 0v2"/></svg></span>Protecting your privacy</div>
  <div class="benefit" style="left:619px;top:399px"><span class="icon"><svg width="34" height="34" viewBox="0 0 34 34" fill="none" stroke="#35577c" stroke-width="1.6"><path d="M4 30h26M7 30V16l7-6 7 6v14M21 30V12h8v18M11 22h6v8h-6z"/></svg></span>More options for housing</div>
</section>

<div class="abs cases-frame"></div>
<div class="photo" style="left:74px;top:3140px;width:542px;height:394px;background:linear-gradient(120deg,#c9d0d6 0%,#eef0f1 40%,#2f3a48 75%,#1c2530 100%)" role="img" aria-label="Two people at a desk reviewing and signing a document"></div>
<h2 class="abs serif" style="left:645px;top:3161px;font-size:47px;line-height:52px;color:var(--ink);font-weight:400">TYPES OF CASES<br>QUALIFY</h2>
<ul class="cases-list">
  <li style="left:645px;top:3284px"><svg width="18" height="18" viewBox="0 0 18 18" style="margin-top:4px;flex:0 0 18px"><circle cx="9" cy="9" r="8" fill="#35577c"/><path d="M5 9l3 3 5-6" stroke="#fff" stroke-width="2" fill="none"/></svg>Criminal accusations that were dismissed</li>
  <li style="left:645px;top:3324px;width:380px"><svg width="18" height="18" viewBox="0 0 18 18" style="margin-top:4px;flex:0 0 18px"><circle cx="9" cy="9" r="8" fill="#35577c"/><path d="M5 9l3 3 5-6" stroke="#fff" stroke-width="2" fill="none"/></svg>Criminal cases that went into a diversionary program</li>
  <li style="left:645px;top:3390px"><svg width="18" height="18" viewBox="0 0 18 18" style="margin-top:4px;flex:0 0 18px"><circle cx="9" cy="9" r="8" fill="#35577c"/><path d="M5 9l3 3 5-6" stroke="#fff" stroke-width="2" fill="none"/></svg>Convictions</li>
</ul>
<a class="btn" style="left:645px;top:3451px;width:179px;height:56px">READ MORE</a>

<section class="abs cta">
  <p>TO SEE IF YOU QUALIFY FOR<br>EXPUNGEMENT OR FOR ADDITIONAL<br>INFORMATION, CONTACT US</p>
  <div class="phone">
    <svg width="34" height="40" viewBox="0 0 22 24" fill="none" stroke="#fff" stroke-width="2"><path d="M5 3l4 1 1 5-3 2c1 3 3 5 6 6l2-3 5 1 1 4c-1 2-3 3-5 3C8 21 2 14 2 7c0-2 1-3 3-4z" fill="#fff"/><path d="M15 3c2 1 3 2 4 4M14 7c1 0 2 1 2 2"/></svg>
    505-555-0142
  </div>
</section>

<footer class="abs footer">
  <div class="brand" style="left:74px;top:136px">
    <span class="brand-square"></span>
    <span class="brand-name">BRIGHTPATH RECORD<br>RENEWAL</span>
  </div>

  <h4 style="left:462px;top:52px">QUICK LINKS</h4>
  <a class="link" style="left:462px;top:96px">Home</a>
  <a class="link" style="left:462px;top:135px">About Us</a>
  <a class="link" style="left:462px;top:173px">Services</a>
  <a class="link" style="left:462px;top:211px">Benefits</a>
  <a class="link" style="left:594px;top:96px">Cases</a>
  <a class="link" style="left:594px;top:135px">Blog</a>
  <a class="link" style="left:594px;top:173px">Contact Us</a>

  <h4 style="left:794px;top:52px">CONTACT INFO</h4>
  <div class="contact" style="top:96px"><svg width="14" height="18" viewBox="0 0 14 18" style="flex:0 0 14px;margin-top:2px"><path d="M7 1a6 6 0 016 6c0 4-6 10-6 10S1 11 1 7a6 6 0 016-6z" fill="#d4a52a"/><circle cx="7" cy="7" r="2" fill="#262626"/></svg><span>Nemo enim ipsam voluptat<br>em quia voluptas</span></div>
  <div class="contact" style="top:157px"><svg width="14" height="16" viewBox="0 0 22 24" style="flex:0 0 14px;margin-top:3px"><path d="M5 3l4 1 1 5-3 2c1 3 3 5 6 6l2-3 5 1 1 4c-1 2-3 3-5 3C8 21 2 14 2 7c0-2 1-3 3-4z" fill="#d4a52a"/></svg><span>505-555-0142</span></div>
  <div class="contact" style="top:196px"><svg width="14" height="12" viewBox="0 0 14 12" style="flex:0 0 14px;margin-top:5px"><rect x="0" y="0" width="14" height="11" fill="#d4a52a"/><path d="M0 1l7 5 7-5" stroke="#262626" fill="none"/></svg><span>hello@brightpathrenewal.com</span></div>
  <div class="social" style="position:absolute;left:794px;top:250px;gap:24px;color:#fff" aria-label="Social links"><span style="width:22px;height:22px"></span><span style="width:22px;height:22px"></span><span style="width:22px;height:22px"></span><span style="width:22px;height:22px"></span><span style="width:22px;height:22px"></span></div>
</footer>

<div class="abs copyright">Copyright 2023 © Company Name All Right Reserved</div>

</body>
</html>
```